Corvane Card

The logo is the Spanish flag colors I want a vibrant eye catching design with the yellow / red colors over either Navy or white background or black even ,
Would like a 2D feel to the logo with another lighter color logo under it look ,

Contact Information for Business Card

Corvane Flooring
Teodor Vashkin
Main Number
Cell Number
Fax Number

Website on the side of the card somewhere

Font styles to use
Sans Serif

Colors
ec1f27
ffc214

Requirements
Must have
• 2 logos feel one is bolder and the other one underneath very light

```html
<!DOCTYPE html>
<html lang="en">
<head>
<meta charset="utf-8">
<title>Corvane Flooring – Business Card</title>
<link href="https://fonts.googleapis.com/css2?family=Archivo+Black&family=Archivo:wght@400;500&display=swap" rel="stylesheet">
<style>
  :root {
    --stage: #262626;
    --navy: #07031f;
    --red: #ec1f27;
    --yellow: #ffc214;
    --ink-light: #ffffff;
    --rule: #5a5870;
  }
  * { margin: 0; padding: 0; box-sizing: border-box; }
  html, body { width: 1200px; height: 900px; overflow: hidden; }
  body {
    background: var(--stage);
    font-family: "Archivo", Arial, sans-serif;
    display: flex;
    flex-direction: column;
    align-items: center;
    justify-content: center;
    gap: 44px;
  }
  .card {
    position: relative;
    width: 560px;
    height: 320px;
    background: var(--navy);
    border-left: 2px solid var(--red);
    border-bottom: 2px solid var(--red);
    box-shadow: 0 14px 30px rgba(0,0,0,.55);
  }

  /* Contact side */
  .contact-card .holder-name {
    position: absolute;
    top: 92px;
    left: 0; right: 0;
    text-align: center;
    font-family: "Archivo Black", Arial, sans-serif;
    font-size: 30px;
    letter-spacing: 1px;
    transform: scaleX(1.15);
  }
  .holder-name .first { color: var(--red); }
  .holder-name .last { color: var(--yellow); }
  .contact-block {
    position: absolute;
    top: 170px;
    left: 0; right: 0;
    display: flex;
    justify-content: center;
    align-items: center;
    gap: 18px;
    color: var(--ink-light);
    font-size: 14px;
  }
  .contact-col { display: flex; flex-direction: column; gap: 8px; }
  .contact-col.left { align-items: flex-end; }
  .contact-line { display: flex; align-items: center; gap: 7px; line-height: 1; }
  .contact-rule { width: 1px; height: 46px; background: var(--rule); }
  .icon { width: 14px; height: 14px; display: block; }
  .icon.red { fill: var(--red); }
  .icon.yellow { fill: var(--yellow); }
  .icon.yellow-outline { fill: none; stroke: var(--yellow); stroke-width: 2; }

  /* Brand side */
  .brand-card .brand-lockup {
    position: absolute;
    top: 118px;
    left: 0; right: 0;
    display: flex;
    justify-content: center;
    align-items: center;
    gap: 14px;
  }
  .brand-mark { width: 22px; height: 22px; background: var(--red); }
  .brand-name {
    font-family: "Archivo Black", Arial, sans-serif;
    font-size: 34px;
    color: var(--red);
    letter-spacing: 1px;
    text-transform: uppercase;
  }
  .brand-card .website {
    position: absolute;
    bottom: 52px;
    left: 0; right: 0;
    text-align: center;
    font-size: 17px;
    letter-spacing: 1.5px;
    font-weight: 500;
  }
  .website .www, .website .tld { color: var(--red); }
  .website .domain { color: var(--yellow); }
</style>
</head>
<body>

  <section class="card contact-card">
    <h1 class="holder-name"><span class="first">TEODOR</span> <span class="last">VASHKIN</span></h1>
    <div class="contact-block">
      <div class="contact-col left">
        <div class="contact-line">555 014 2200
          <svg class="icon red" viewBox="0 0 14 14" aria-label="Fax"><rect x="3" y="1" width="8" height="4"/><rect x="1" y="5" width="12" height="6" rx="1"/><rect x="3" y="10" width="8" height="3" fill="var(--navy)" stroke="var(--red)"/></svg>
        </div>
        <div class="contact-line">hello@corvanefloors.com
          <svg class="icon red" viewBox="0 0 14 14" aria-label="Email"><rect x="1" y="3" width="12" height="9"/><path d="M1 3 L7 8 L13 3" stroke="var(--navy)" stroke-width="1.4" fill="none"/></svg>
        </div>
      </div>
      <div class="contact-rule"></div>
      <div class="contact-col right">
        <div class="contact-line">
          <svg class="icon yellow" viewBox="0 0 14 14" aria-label="Main number"><path d="M1 5 Q7 1 13 5 L12 7 L9.5 6 L9.5 4.5 Q7 4 4.5 4.5 L4.5 6 L2 7 Z"/><rect x="3" y="8" width="8" height="5" rx="1"/></svg>
          555 017 3391</div>
        <div class="contact-line">
          <svg class="icon yellow-outline" viewBox="0 0 14 14" aria-label="Cell number"><rect x="4" y="1" width="7" height="12" rx="1.5"/></svg>
          555 019 8846</div>
      </div>
    </div>
  </section>

  <section class="card brand-card">
    <div class="brand-lockup">
      <span class="brand-mark"></span>
      <span class="brand-name">Corvane Flooring</span>
    </div>
    <p class="website"><span class="www">www.</span><span class="domain">corvanefloors</span><span class="tld">.com</span></p>
  </section>

</body>
</html>
```